Business card for marketing analytics company

Need a business card for new company. I have a logo already that I want to be built into the card and should use those colours

Company is called steered by tallies
Design must bring steered by tallies to life not be a card that could be for anyone with a logo put on it.

Like the front to be fairly clean and uncluttered bringing the logo out with a suitable design on the back of the card.

The logo represents a compass and business growth so those themes along with numbers, analytics , data are appropriate.
I'm often working with creative industries so also needs to reflect the creative side of analytics rather than be very corporate looking.

Target Market(s)

Ad agency, media agency, consumer goods clients

Industry/Entity Type

Market Research

Contact Information for Business Card

Needs to include name, title, email and phone number

Colors
f78f20
f68d4d
ec1f27

Requirements
Must have
• Must bring steered by tallies to life not be a card that could be for anyone with a logo put on it.
• Logo, Correct colours
• Like a design on the back that relates to company name
• Designs for both sides
Should not have
• Please do not just submit logo and a coloured card.
• It needs to have a design element to it
• No black background
• No clear cards - needs front & back

```html
<!DOCTYPE html>
<html lang="en">
<head>
<meta charset="utf-8">
<title>Quillmere Insight – Business Card</title>
<link rel="stylesheet" href="https://fonts.googleapis.com/css2?family=Lato:wght@400;700;900&display=swap">
<style>
  :root{
    --orange:#f78f20;
    --orange-deep:#f4761f;
    --orange-shade:#c9641c;
    --coral:#f68d4d;
    --red:#ec1f27;
    --ink:#3d4347;
    --ink-soft:#4a5055;
    --paper:#ffffff;
    --paper-cool:#f7f8fa;
    --stage:#e7e4e1;
  }
  *{box-sizing:border-box;margin:0;padding:0}
  html,body{width:1200px;height:1000px;overflow:hidden}
  body{background:var(--stage);font-family:"Lato",Arial,sans-serif;position:relative}

  .card{
    position:absolute;width:540px;height:300px;border-radius:26px;overflow:hidden;
    box-shadow:0 10px 28px rgba(0,0,0,.18);
  }

  /* Front */
  .card--front{left:110px;top:150px;background:var(--paper)}
  .front-brand{
    position:absolute;left:40px;top:0;bottom:0;width:220px;
    display:flex;align-items:center;gap:12px;
  }
  .front-brand__dot{width:22px;height:22px;border-radius:50%;background:var(--red);flex:none}
  .front-brand__name{font-weight:900;font-size:26px;line-height:1.1;color:var(--red)}

  .contact{position:absolute;left:285px;top:86px}
  .contact__name{font-weight:900;font-size:25px;letter-spacing:.2px;color:var(--ink)}
  .contact__name .surname{color:var(--red)}
  .contact__title{font-size:19px;color:var(--ink-soft);margin-top:2px}
  .contact__list{list-style:none;margin-top:20px}
  .contact__item{display:flex;align-items:center;gap:10px;font-size:13.5px;color:var(--ink);margin-bottom:10px}
  .contact__icon{width:22px;height:22px;border-radius:50%;background:var(--orange);display:flex;align-items:center;justify-content:center;flex:none}

  /* Back */
  .card--back{left:550px;top:540px;background:var(--orange)}
  .back-field{position:absolute;inset:0;background:linear-gradient(135deg,var(--orange) 0%,var(--orange-deep) 100%)}
  .back-peaks{position:absolute;inset:0}
  .back-brand{
    position:absolute;right:30px;bottom:34px;display:flex;align-items:center;gap:12px;
  }
  .back-brand__dot{width:26px;height:26px;border-radius:50%;background:var(--red);flex:none}
  .back-brand__name{font-weight:900;font-size:25px;line-height:1.05;color:var(--orange-deep);text-align:right}
</style>
</head>
<body>

<section class="card card--front" aria-label="Card front">
  <div class="front-brand">
    <span class="front-brand__dot"></span>
    <span class="front-brand__name">Quillmere<br>Insight</span>
  </div>

  <div class="contact">
    <p class="contact__name">JOHN <span class="surname">DOE</span></p>
    <p class="contact__title">Director</p>
    <ul class="contact__list">
      <li class="contact__item">
        <span class="contact__icon">
          <svg width="12" height="12" viewBox="0 0 24 24"><path fill="#fff" d="M6.6 10.8a15 15 0 0 0 6.6 6.6l2.2-2.2a1 1 0 0 1 1-.25 11.4 11.4 0 0 0 3.6.57 1 1 0 0 1 1 1V20a1 1 0 0 1-1 1A17 17 0 0 1 3 4a1 1 0 0 1 1-1h3.5a1 1 0 0 1 1 1c0 1.25.2 2.45.57 3.6a1 1 0 0 1-.25 1z"/></svg>
        </span>
        (01) 123 456 7890
      </li>
      <li class="contact__item">
        <span class="contact__icon">
          <svg width="12" height="12" viewBox="0 0 24 24"><rect x="2" y="5" width="20" height="14" rx="2" fill="#fff"/><path d="M3 6l9 7 9-7" stroke="#f78f20" stroke-width="2" fill="none"/></svg>
        </span>
        youremailaddress@domain.com
      </li>
      <li class="contact__item">
        <span class="contact__icon">
          <svg width="12" height="12" viewBox="0 0 24 24" fill="none" stroke="#fff" stroke-width="2"><circle cx="12" cy="12" r="9"/><path d="M3 12h18M12 3c3 3 3 15 0 18M12 3c-3 3-3 15 0 18"/></svg>
        </span>
        www.yourwebsite.com
      </li>
    </ul>
  </div>
</section>

<section class="card card--back" aria-label="Card back">
  <div class="back-field" role="img" aria-label="Orange field with a faint repeating pattern of small brand marks and dots"></div>
  <svg class="back-peaks" viewBox="0 0 540 300" preserveAspectRatio="none" aria-hidden="true">
    <polygon points="300,48 318,48 396,176 387,186" fill="var(--orange-shade)"/>
    <polygon points="140,300 300,48 387,186 540,22 540,300" fill="var(--paper-cool)"/>
  </svg>
  <div class="back-brand">
    <span class="back-brand__dot"></span>
    <span class="back-brand__name">Quillmere<br>Insight</span>
  </div>
</section>

</body>
</html>
```